Harrow Grading LLC business card design

Excavation company business cards

Contact Information for Business Card

Harrow Grading LLC cell phone 208-417-6290 office phone 208-319-4856 harrowgradingllc@maplecove.com Driveways, site prep, retaining walls, septic systems, rock delivery

Colors

Designer to choose colors to be used in the design.

```html
<!DOCTYPE html>
<html lang="en">
<head>
<meta charset="utf-8">
<title>Harrow Grading LLC — Business Card</title>
<link href="https://fonts.googleapis.com/css2?family=Roboto:ital,wght@0,400;0,700;1,400&display=swap" rel="stylesheet">
<style>
  :root {
    --page: #e9e9e9;
    --card-white: #ffffff;
    --card-grey: #666666;
    --orange: #ee7523;
    --ink: #1e1e1e;
    --rule: #6b6b6b;
    --back-mark: #4a4a4a;
    --back-text: #f2f2f2;
  }
  * { margin: 0; padding: 0; box-sizing: border-box; }
  html, body { width: 1200px; height: 1200px; overflow: hidden; }
  body {
    background: var(--page);
    font-family: "Roboto", Arial, sans-serif;
    display: flex;
    align-items: center;
    justify-content: center;
    gap: 70px;
  }
  .card {
    width: 420px;
    height: 720px;
    border-radius: 30px;
    position: relative;
    overflow: hidden;
    box-shadow: 0 6px 18px rgba(0,0,0,0.18);
  }

  /* Front */
  .card-front { background: var(--card-white); }
  .brand {
    position: absolute;
    top: 150px; left: 0; right: 0;
    display: flex; align-items: center; justify-content: center; gap: 12px;
  }
  .brand-mark { width: 22px; height: 22px; background: var(--orange); }
  .brand-name {
    font-weight: 700; font-size: 34px; color: var(--orange);
    letter-spacing: 0.5px;
  }
  .person {
    position: absolute; top: 380px; left: 0; right: 0; text-align: center;
  }
  .person-name {
    font-weight: 700; font-size: 27px; color: var(--orange); letter-spacing: 0.5px;
  }
  .person-title {
    font-style: italic; font-size: 21px; color: var(--ink); margin-top: 2px;
  }
  .icon-row {
    position: absolute; top: 478px; left: 30px; right: 30px;
    display: flex; align-items: center; gap: 8px;
  }
  .icon-row .rule { flex: 1; height: 1px; background: var(--rule); }
  .icon-row .icons { display: flex; gap: 6px; padding: 0 4px; }
  .icon {
    width: 26px; height: 26px; border-radius: 4px; background: var(--orange);
    display: flex; align-items: center; justify-content: center;
  }
  .contact {
    position: absolute; top: 525px; left: 0; right: 0; text-align: center;
    font-size: 19px; line-height: 29px; color: var(--ink);
  }
  .contact .tag { color: var(--orange); font-size: 14px; }

  /* Back */
  .card-back { background: var(--card-grey); }
  .back-brand {
    position: absolute; left: 50%; top: 50%;
    transform: translate(-50%, -50%) rotate(-90deg);
    display: flex; align-items: center; gap: 16px; white-space: nowrap;
  }
  .back-brand .brand-mark { width: 34px; height: 34px; background: var(--back-mark); }
  .back-brand .brand-name { font-size: 54px; color: var(--back-mark); }
  .services {
    position: absolute; right: 36px; top: 50%;
    transform: translate(50%, -50%) rotate(-90deg);
    transform-origin: center;
    white-space: nowrap;
    font-size: 19px; color: var(--back-text); letter-spacing: 0.3px;
  }
  .services .dot { color: var(--orange); margin: 0 6px; }
</style>
</head>
<body>
  <section class="card card-front">
    <div class="brand">
      <span class="brand-mark"></span>
      <span class="brand-name">HARROW GRADING</span>
    </div>

    <div class="person">
      <div class="person-name">DALEN WHITCOMBE</div>
      <div class="person-title">Founder</div>
    </div>

    <div class="icon-row">
      <span class="rule"></span>
      <div class="icons">
        <span class="icon" aria-label="phone">
          <svg width="16" height="16" viewBox="0 0 24 24"><path fill="#fff" d="M6.6 10.8a15.1 15.1 0 0 0 6.6 6.6l2.2-2.2a1 1 0 0 1 1-.25 11.4 11.4 0 0 0 3.6.57 1 1 0 0 1 1 1V20a1 1 0 0 1-1 1A17 17 0 0 1 3 4a1 1 0 0 1 1-1h3.5a1 1 0 0 1 1 1c0 1.25.2 2.45.57 3.6a1 1 0 0 1-.25 1z"/></svg>
        </span>
        <span class="icon" aria-label="mobile">
          <svg width="16" height="16" viewBox="0 0 24 24"><rect x="6.5" y="2" width="11" height="20" rx="2" fill="none" stroke="#fff" stroke-width="2"/><circle cx="12" cy="18" r="1.2" fill="#fff"/></svg>
        </span>
        <span class="icon" aria-label="email">
          <svg width="16" height="16" viewBox="0 0 24 24"><rect x="3" y="5" width="18" height="14" fill="none" stroke="#fff" stroke-width="2"/><path d="M3 5l9 8 9-8" fill="none" stroke="#fff" stroke-width="2"/></svg>
        </span>
        <span class="icon" aria-label="website">
          <svg width="16" height="16" viewBox="0 0 24 24"><circle cx="12" cy="12" r="9" fill="none" stroke="#fff" stroke-width="2"/><path d="M3 12h18M12 3c3 3 3 15 0 18M12 3c-3 3-3 15 0 18" fill="none" stroke="#fff" stroke-width="1.5"/></svg>
        </span>
      </div>
      <span class="rule"></span>
    </div>

    <div class="contact">
      <div>208-319-4856 <span class="tag">(office)</span></div>
      <div>208-417-6290</div>
      <div>harrowgradingllc@maplecove.com</div>
      <div>www.harrowgradingllc.com</div>
    </div>
  </section>

  <section class="card card-back">
    <div class="back-brand">
      <span class="brand-mark"></span>
      <span class="brand-name">HARROW GRADING</span>
    </div>
    <div class="services">
      Driveways<span class="dot">•</span>Site Prep<span class="dot">•</span>Retaining Walls<span class="dot">•</span>Septic Systems<span class="dot">•</span>Rock Delivery
    </div>
  </section>
</body>
</html>
```